NimbaVault Website Homepage Design

Please provide your idea of homepage for a hosting company. This project is for DESIGN only, no coding.

It must use/combine colors used in logo, clean, modern look.

Homepage must consist of at least 4 sections (example: testimonials, services, and so on. not necesarily all of them). We would like the navigation to be horizontal, but not mandatory.

You can include a preview of services page (optional, not a must).

Number of Pages Required

1 page

Font styles to use
Sans Serif

```html
<!DOCTYPE html>
<html lang="en">
<head>
<meta charset="utf-8">
<title>NimbaVault Homepage</title>
<link rel="stylesheet" href="https://fonts.googleapis.com/css2?family=Montserrat:ital,wght@0,400;0,500;0,600;0,700;1,400;1,500&display=swap">
<style>
:root{
  --blue:#0a7fd9;
  --blue-deep:#0078db;
  --blue-light:#12a0e6;
  --grey:#f1f1f1;
  --text:#555;
  --white:#fff;
  --placeholder:#999;
}
*{box-sizing:border-box;margin:0;padding:0}
html,body{width:1200px;height:1200px;overflow:hidden;background:var(--white)}
body{position:relative;font-family:'Montserrat',sans-serif;color:var(--blue)}
.abs{position:absolute}

/* ---------- desktop ---------- */
.desktop{position:absolute;left:66px;top:0;width:601px;height:1200px}
.d-hero{position:absolute;left:0;top:49px;width:601px;height:265px;overflow:hidden;background:linear-gradient(120deg,var(--blue-deep) 0%,#0a88dd 60%,var(--blue-light) 100%)}
.d-hero svg{position:absolute;inset:0}
.hero-title{position:absolute;left:0;width:100%;text-align:center;color:var(--white);font-weight:600;letter-spacing:2px}
.d-hero .hero-title{top:52px;font-size:19.5px;left:-7px}
.hero-rule{position:absolute;height:2px;background:var(--white)}
.quote{position:absolute;color:var(--white);font-style:italic;text-align:center}
.d-hero .quote{left:125px;width:346px;top:113px;font-size:10.4px;line-height:12.5px}
.author{position:absolute;left:0;width:100%;text-align:center;top:193px;color:var(--white);font-style:italic;font-size:10.5px;letter-spacing:1px;left:-7px}
.chev{position:absolute;width:10px;height:14px}

.d-grey{position:absolute;left:0;top:331px;width:601px;height:869px}
.photo{position:absolute;background:linear-gradient(135deg,#3b342c 0%,#8b6a45 35%,#c49a5d 55%,#d8d3cd 80%,#6f5b48 100%)}
.d-photo{left:68px;top:386px;width:230px;height:153px}

.section-title{position:absolute;font-weight:700;letter-spacing:2px;color:var(--blue);line-height:1.05}
.d-why{left:322px;top:384px;font-size:20.5px}
.feature{position:absolute;left:313px;display:flex;align-items:center;gap:6px}
.icon{width:15px;height:15px;border-radius:50%;background:var(--blue);display:flex;align-items:center;justify-content:center;flex:none}
.icon svg{width:70%;height:70%}
.feature p{font-size:6.3px;line-height:7.5px;color:var(--blue)}

.d-questions{left:0;width:601px;text-align:center;top:620px;font-size:19.5px}
.sub-title{position:absolute;font-weight:600;letter-spacing:1.5px;color:var(--blue)}
.faq-q{position:absolute;font-weight:600;font-size:8.6px;letter-spacing:.6px;color:var(--blue)}
.faq-a{position:absolute;font-size:6.3px;line-height:7.6px;color:var(--text)}
.d-faq-a{left:79px;width:225px}

.field{position:absolute;left:336px;width:195px;background:var(--white);font-size:8px;color:var(--placeholder);padding:3px 7px;letter-spacing:.5px}
.submit{position:absolute;left:478px;top:851px;width:53px;height:14px;background:var(--blue);color:var(--white);font-size:7px;font-weight:600;letter-spacing:.6px;display:flex;align-items:center;justify-content:center}
.info-line{position:absolute;left:370px;font-size:6.2px;color:var(--text)}
.line-icon{position:absolute;left:339px;width:16px;height:14px}

.brand{position:absolute;font-weight:700;color:var(--blue);letter-spacing:1px}
.d-brand{left:0;width:601px;text-align:center;top:1092px;font-size:30px}
.d-footer{position:absolute;left:0;top:1152px;width:601px;height:48px;background:var(--blue-deep)}

/* ---------- mobile ---------- */
.mobile{position:absolute;left:817px;top:0;width:196px;height:1200px}
.m-hero{position:absolute;left:0;top:56px;width:196px;height:260px;overflow:hidden;background:linear-gradient(120deg,var(--blue-deep) 0%,#0a88dd 70%,var(--blue-light) 100%)}
.m-hero svg{position:absolute;inset:0}
.m-hero .hero-title{top:45px;font-size:12px;line-height:15px;letter-spacing:1.2px}
.m-hero .quote{left:16px;width:164px;top:101px;font-size:6.3px;line-height:8.45px}
.m-photo{left:0;top:316px;width:196px;height:103px}
.m-why{left:0;width:196px;text-align:center;top:432px;font-size:17.5px}
.m-feature{position:absolute;width:82px;text-align:center}
.m-feature .icon{width:25px;height:25px;margin:0 auto 11px}
.m-feature p{font-size:5.6px;line-height:7.15px;color:var(--blue)}
.m-grey{position:absolute;left:0;top:807px;width:196px;height:393px;background:var(--grey)}
.m-questions{left:0;width:196px;text-align:center;top:821px;font-size:17.5px}
.m-faq-a{left:13px;width:175px}
</style>
</head>
<body>

<!-- DESKTOP -->
<section class="desktop">
  <div class="d-hero">
    <svg viewBox="0 0 601 265" preserveAspectRatio="none" aria-hidden="true">
      <path d="M420 0 C560 40 520 170 601 200 L601 0 Z" fill="#1aa2e8" opacity=".35"/>
      <path d="M250 265 C330 190 470 210 601 120 L601 265 Z" fill="#1aa2e8" opacity=".3"/>
    </svg>
    <h2 class="hero-title">WHAT OUR CUSTOMERS SAY.</h2>
    <div class="hero-rule" style="left:125px;top:80px;width:347px"></div>
    <p class="quote">Lorem ipsum dolor sit amet, consectetur adipiscing elit, sed" do eiusmod tempor incididunt ut labore et dolore magna aliqua. Ut enim ad minim veniam, quis nostrud exercitation ullamco laboris nisi ut aliquip ex ea commodo consequat.</p>
    <p class="author">-John Doe</p>
    <svg class="chev" style="left:59px;top:132px" viewBox="0 0 10 14"><path d="M7 2 L2 7 L7 12" fill="none" stroke="#fff" stroke-width="1.8"/></svg>
    <svg class="chev" style="left:533px;top:132px" viewBox="0 0 10 14"><path d="M3 2 L8 7 L3 12" fill="none" stroke="#fff" stroke-width="1.8"/></svg>
  </div>

  <svg class="abs" style="left:0;top:331px" width="601" height="821" aria-hidden="true">
    <path d="M601 0 L601 821 L0 821 L0 302 Z" fill="var(--grey)"/>
  </svg>

  <div class="photo d-photo" role="img" aria-label="Photo of a person in a mustard sweater typing on a laptop at a wooden desk"></div>

  <h2 class="section-title d-why">WHY CHOOSE<br>NIMBAVAULT?</h2>

  <div class="feature" style="top:437px"><span class="icon"><svg viewBox="0 0 10 10"><path d="M2 6 V5 A3 3 0 0 1 8 5 V6" fill="none" stroke="#fff" stroke-width=".8"/><rect x="1.5" y="5.5" width="1.5" height="2" fill="#fff"/><rect x="7" y="5.5" width="1.5" height="2" fill="#fff"/></svg></span><p>Lorem ipsum dolor sit amet, consectetur adipiscing"<br>elit, sed do eiusmod tempor incididunt ut labore et</p></div>
  <div class="feature" style="top:460px"><span class="icon"><svg viewBox="0 0 10 10"><circle cx="5" cy="5" r="3" fill="none" stroke="#fff" stroke-width=".8" stroke-dasharray="1.2 .6"/><circle cx="5" cy="5" r="1.2" fill="none" stroke="#fff" stroke-width=".7"/></svg></span><p>Lorem ipsum dolor sit amet, consectetur adipiscing"</p></div>
  <div class="feature" style="top:479px"><span class="icon"><svg viewBox="0 0 10 10"><circle cx="5.5" cy="5.5" r="3" fill="none" stroke="#fff" stroke-width=".8"/><path d="M5.5 4 V5.5 L6.7 6.3 M4.5 1.5 H6.5" fill="none" stroke="#fff" stroke-width=".7"/></svg></span><p>Lorem ipsum dolor sit amet, consectetur adipiscing"</p></div>
  <div class="feature" style="top:499px"><span class="icon"><svg viewBox="0 0 10 10"><path d="M3 8 L3 4 L5 2 L5 5 L7 4 L7 8 Z" fill="none" stroke="#fff" stroke-width=".7"/></svg></span><p>Lorem ipsum dolor sit amet, consectetur adipiscing"</p></div>
  <div class="feature" style="top:521px"><span class="icon"><svg viewBox="0 0 10 10"><circle cx="5" cy="4.5" r="3" fill="none" stroke="#fff" stroke-width=".8"/><circle cx="5" cy="4.5" r="1.3" fill="none" stroke="#fff" stroke-width=".7"/><path d="M3.5 7 L3 9 M6.5 7 L7 9" stroke="#fff" stroke-width=".7"/></svg></span><p>Lorem ipsum dolor sit amet, consectetur adipiscing"<br>elit, sed do eiusmod tempor incididunt ut labore et</p></div>

  <h2 class="section-title d-questions">GOT QUESTIONS?</h2>

  <h3 class="sub-title" style="left:83px;top:683px;font-size:13.5px">FAQ</h3>
  <h4 class="faq-q" style="left:79px;top:713px">¿Lorem ipsum dolor sit amet?</h4>
  <p class="faq-a d-faq-a" style="top:729px">Lorem ipsum dolor sit amet, consectetur adipiscing elit, sed do eius-" mod tempor incididunt ut labore et dolore magna aliqua. Ut enim ad minim veniam, quis nostrud exercitation ullamco laboris nisi ut aliquip ex ea commodo consequat. Duis aute irure dolor in reprehenderit in voluptate velit esse cillum dolore eu fugiat nulla pariatur. Ex-</p>
  <h4 class="faq-q" style="left:79px;top:792px">¿Lorem ipsum dolor sit amet?</h4>
  <p class="faq-a d-faq-a" style="top:810px">Lorem ipsum dolor sit amet, consectetur adipiscing elit, sed do eius-" mod tempor incididunt ut labore et dolore magna aliqua. Ut enim ad minim veniam, quis nostrud exercitation ullamco laboris nisi ut aliquip ex ea commodo consequat. Duis aute irure dolor in reprehenderit in voluptate velit esse cillum dolore eu fugiat nulla pariatur. Ex-</p>
  <h4 class="faq-q" style="left:79px;top:872px">¿Lorem ipsum dolor sit amet?</h4>
  <p class="faq-a d-faq-a" style="top:890px">Lorem ipsum dolor sit amet, consectetur adipiscing elit, sed do eius-" mod tempor incididunt ut labore et dolore magna aliqua. Ut enim ad minim veniam, quis nostrud exercitation ullamco laboris nisi ut aliquip ex ea commodo consequat. Duis aute irure dolor in reprehenderit in voluptate velit esse cillum dolore eu fugiat nulla pariatur. Ex-</p>
  <h4 class="faq-q" style="left:79px;top:951px">¿Lorem ipsum dolor sit amet?</h4>
  <p class="faq-a d-faq-a" style="top:968px">Lorem ipsum dolor sit amet, consectetur adipiscing elit, sed do eius-" mod tempor incididunt ut labore et dolore magna aliqua. Ut enim ad minim veniam, quis nostrud exercitation ullamco laboris nisi ut aliquip ex ea commodo consequat. Duis aute irure dolor in reprehenderit in voluptate velit esse cillum dolore eu fugiat nulla pariatur. Ex-</p>

  <h3 class="sub-title" style="left:336px;top:680px;font-size:14px">Contact us</h3>
  <div class="field" style="top:729px;height:15px">Name...</div>
  <div class="field" style="top:752px;height:15px">email...</div>
  <div class="field" style="top:774px;height:65px">Message...</div>
  <div class="submit">Submit</div>

  <h3 class="sub-title" style="left:336px;top:904px;font-size:13.5px">Contact Info.</h3>
  <p class="faq-a" style="left:336px;top:928px;width:200px">Lorem ipsum dolor sit amet, consectetur adipiscing"<br>elit, sed do eiusmod tempor incididunt ut labore et</p>
  <svg class="line-icon" style="top:956px" viewBox="0 0 16 14" aria-hidden="true"><rect x="1" y="2" width="14" height="10" fill="none" stroke="var(--blue)" stroke-width=".9"/><path d="M1 2 L8 8 L15 2 M1 12 L6 7 M15 12 L10 7" fill="none" stroke="var(--blue)" stroke-width=".9"/></svg>
  <p class="info-line" style="top:959px">Lorem ipsum dolor sit amet,"</p>
  <svg class="line-icon" style="top:987px" viewBox="0 0 16 14" aria-hidden="true"><path d="M3 1.5 L5.5 1.5 L6.5 4.5 L5 5.5 C6 8 7.5 9.5 10 10.5 L11 9 L14 10 L14 12.5 C8 13 2.5 7.5 3 1.5 Z" fill="none" stroke="var(--blue)" stroke-width=".9" stroke-linejoin="round"/></svg>
  <p class="info-line" style="top:992px">Lorem ipsum dolor sit amet,"</p>

  <div class="brand d-brand">NIMBAVAULT</div>
  <div class="d-footer"></div>
</section>

<!-- MOBILE -->
<section class="mobile">
  <div class="m-hero">
    <svg viewBox="0 0 196 260" preserveAspectRatio="none" aria-hidden="true">
      <path d="M150 0 C196 40 170 120 196 150 L196 0 Z" fill="#1aa2e8" opacity=".35"/>
      <path d="M60 260 C110 200 160 210 196 170 L196 260 Z" fill="#1aa2e8" opacity=".3"/>
    </svg>
    <h2 class="hero-title">WHAT OUR<br>CUSTOMERS SAY.</h2>
    <div class="hero-rule" style="left:57px;top:80px;width:82px;height:1.2px"></div>
    <p class="quote">Lorem ipsum dolor sit amet, consectetur ad-" ipiscing elit, sed do eiusmod tempor incididunt ut labore et dolore magna aliqua. Ut enim ad minim veniam, quis nostrud exercitation ullamco laboris nisi ut aliquip ex ea commodo consequat. Duis aute irure dolor in reprehenderit in voluptate velit esse cillum dolore eu fugiat nulla pariatur. Excepteur sint occaecat cupidatat non proident, sunt in culpa qui officia deserunt mollit anim id est ".laborum</p>
    <svg class="chev" style="left:6px;top:143px;width:7px;height:10px" viewBox="0 0 10 14"><path d="M7 2 L2 7 L7 12" fill="none" stroke="#fff" stroke-width="2"/></svg>
    <svg class="chev" style="left:183px;top:143px;width:7px;height:10px" viewBox="0 0 10 14"><path d="M3 2 L8 7 L3 12" fill="none" stroke="#fff" stroke-width="2"/></svg>
  </div>
  <div class="photo m-photo" role="img" aria-label="Photo of a person in a mustard sweater typing on a laptop"></div>

  <h2 class="section-title m-why">WHY CHOOSE<br>NIMBAVAULT?</h2>

  <div class="m-feature" style="left:15px;top:490px"><span class="icon"><svg viewBox="0 0 10 10"><path d="M2 6 V5 A3 3 0 0 1 8 5 V6" fill="none" stroke="#fff" stroke-width=".7"/><rect x="1.5" y="5.5" width="1.5" height="2" fill="#fff"/><rect x="7" y="5.5" width="1.5" height="2" fill="#fff"/></svg></span><p>Lorem ipsum dolor sit" amet, consectetur adipiscing elit, sed do eiusmod tempor incididunt ut labore et dolore magna aliqua. Ut enim ad minim veniam, quis nostrud exer-</p></div>
  <div class="m-feature" style="left:110px;top:490px"><span class="icon"><svg viewBox="0 0 10 10"><circle cx="5" cy="5" r="3" fill="none" stroke="#fff" stroke-width=".7" stroke-dasharray="1.2 .6"/><circle cx="5" cy="5" r="1.2" fill="none" stroke="#fff" stroke-width=".6"/></svg></span><p>Lorem ipsum dolor sit" amet, consectetur adipiscing elit, sed do eiusmod tempor incididunt ut labore et dolore magna aliqua. Ut enim ad minim veniam, quis nostrud exer-</p></div>
  <div class="m-feature" style="left:15px;top:601px"><span class="icon"><svg viewBox="0 0 10 10"><circle cx="5.5" cy="5.5" r="3" fill="none" stroke="#fff" stroke-width=".7"/><path d="M5.5 4 V5.5 L6.7 6.3 M4.5 1.5 H6.5" fill="none" stroke="#fff" stroke-width=".6"/></svg></span><p>Lorem ipsum dolor sit" amet, consectetur adipiscing elit, sed do eiusmod tempor incididunt ut labore et dolore magna aliqua. Ut enim ad minim veniam, quis nostrud exer-</p></div>
  <div class="m-feature" style="left:110px;top:601px"><span class="icon"><svg viewBox="0 0 10 10"><path d="M3 8 L3 4 L5 2 L5 5 L7 4 L7 8 Z" fill="none" stroke="#fff" stroke-width=".6"/></svg></span><p>Lorem ipsum dolor sit" amet, consectetur adipiscing elit, sed do eiusmod tempor incididunt ut labore et dolore magna aliqua. Ut enim ad minim veniam, quis nostrud exer-</p></div>
  <div class="m-feature" style="left:57px;top:705px"><span class="icon"><svg viewBox="0 0 10 10"><circle cx="5" cy="4.5" r="3" fill="none" stroke="#fff" stroke-width=".7"/><circle cx="5" cy="4.5" r="1.3" fill="none" stroke="#fff" stroke-width=".6"/><path d="M3.5 7 L3 9 M6.5 7 L7 9" stroke="#fff" stroke-width=".6"/></svg></span><p>Lorem ipsum dolor sit" amet, consectetur adipiscing elit, sed do eiusmod tempor incididunt ut labore et dolore magna aliqua. Ut enim ad minim veniam, quis nostrud exer-</p></div>

  <div class="m-grey"></div>
  <h2 class="section-title m-questions">GOT QUESTIONS?</h2>
  <h3 class="sub-title" style="left:17px;top:855px;font-size:13px">FAQ</h3>

  <h4 class="faq-q" style="left:13px;top:885px">¿Lorem ipsum dolor sit amet?</h4>
  <p class="faq-a m-faq-a" style="top:899px">Lorem ipsum dolor sit amet, consectetur adipiscing" elit, sed do eiusmod tempor incididunt ut labore et dolore magna aliqua. Ut enim ad minim veniam, quis nostrud exercitation ullamco laboris nisi ut aliquip ex ea commodo consequat. Duis aute irure dolor in rep-</p>
  <h4 class="faq-q" style="left:13px;top:964px">¿Lorem ipsum dolor sit amet?</h4>
  <p class="faq-a m-faq-a" style="top:981px">Lorem ipsum dolor sit amet, consectetur adipiscing" elit, sed do eiusmod tempor incididunt ut labore et dolore magna aliqua. Ut enim ad minim veniam, quis nostrud exercitation ullamco laboris nisi ut aliquip ex ea commodo consequat. Duis aute irure dolor in rep-</p>
  <h4 class="faq-q" style="left:13px;top:1045px">¿Lorem ipsum dolor sit amet?</h4>
  <p class="faq-a m-faq-a" style="top:1062px">Lorem ipsum dolor sit amet, consectetur adipiscing" elit, sed do eiusmod tempor incididunt ut labore et dolore magna aliqua. Ut enim ad minim veniam, quis nostrud exercitation ullamco laboris nisi ut aliquip ex ea commodo consequat. Duis aute irure dolor in rep-</p>
  <h4 class="faq-q" style="left:13px;top:1124px">¿Lorem ipsum dolor sit amet?</h4>
  <p class="faq-a m-faq-a" style="top:1141px">Lorem ipsum dolor sit amet, consectetur adipiscing" elit, sed do eiusmod tempor incididunt ut labore et dolore magna aliqua. Ut enim ad minim veniam, quis nostrud exercitation ullamco laboris nisi ut aliquip ex ea commodo consequat. Duis aute irure dolor in rep-</p>
</section>

</body>
</html>
```